Building company buisness cards

We are looking for a sharp modern new look for our business cards.
We are a New Zealand based company that specialises in house and land packages.
We have attached a photo of the current logo and would like to see if it can be improved somehow if needed.
We are open to any colours but we have chosen green at this stage.
Feel free to change the font and make the logo smarter looking.
Play with the colours and see what looks best.

We want a card that looks so good know one will want to throw it away!

Target Market(s)

Home buyers

Industry/Entity Type

Building

Contact Information for Business Card

Derek Tolvane
0217394062
dtolvane@quillmarkhomesteads.co.nz
quillmarkhomesteads.co.nz

Font styles to use
Serif
Sans Serif

Colors

Designer to choose colors to be used in the design.

Requirements
Must have
• Logo and company name on one side, details on the other side
Nice to have
• Color codes for the original green are HEX #4a8028, RGB(74,128,40), CMYK(42,0,69,50)
• Round corners, Raised and/or spot UV

```html
<!DOCTYPE html>
<html lang="en">
<head>
<meta charset="utf-8">
<title>Quillmark Homesteads – Business Cards</title>
<link rel="stylesheet" href="https://fonts.googleapis.com/css2?family=Montserrat:wght@600&family=Roboto:wght@400&display=swap">
<style>
  :root {
    --brand-green: #4a8028;
    --swoosh-grey: #6d6d6d;
    --paper: #ffffff;
    --backdrop: #e4e6e3;
  }
  * { margin: 0; padding: 0; box-sizing: border-box; }
  html, body { width: 1200px; height: 900px; overflow: hidden; background: var(--backdrop); }
  .canvas { position: relative; width: 1200px; height: 900px; }

  .card {
    position: absolute; left: 250px; width: 700px; height: 400px;
    border-radius: 26px; overflow: hidden;
    box-shadow: 0 6px 18px rgba(0,0,0,.18);
  }
  .card--brand { top: 35px; background: var(--brand-green); color: var(--paper); }
  .card--details { top: 465px; background: var(--paper); }

  .company-name {
    font-family: 'Montserrat', sans-serif; font-weight: 600;
    line-height: 1; white-space: nowrap;
  }

  .card--brand .company-name {
    position: absolute; top: 165px; left: 0; width: 100%;
    text-align: center; font-size: 48px;
  }
  .card--brand .site {
    position: absolute; top: 290px; width: 100%; text-align: center;
    font-family: 'Roboto', sans-serif; font-size: 17px; letter-spacing: .5px;
  }

  .card--details .company-name {
    position: absolute; top: 62px; left: 44px;
    font-size: 34px; color: var(--brand-green);
  }

  .wave { position: absolute; inset: 0; }

  .contact {
    position: absolute; right: 40px; top: 282px; text-align: right;
    color: var(--paper); font-family: 'Roboto', sans-serif;
  }
  .contact .name { font-family: 'Montserrat', sans-serif; font-weight: 600; font-size: 26px; line-height: 1; }
  .contact .role { font-size: 15px; line-height: 18px; margin-bottom: 2px; }
  .contact ul { list-style: none; }
  .contact li { display: flex; justify-content: flex-end; align-items: center; gap: 10px; font-size: 15px; line-height: 21px; }
  .contact svg { width: 14px; height: 14px; }
</style>
</head>
<body>
<main class="canvas">

  <section class="card card--brand" aria-label="Card front">
    <p class="company-name">quillmark homesteads.</p>
    <p class="site">www.quillmarkhomesteads.co.nz</p>
  </section>

  <section class="card card--details" aria-label="Card back">
    <svg class="wave" viewBox="0 0 700 400" aria-hidden="true">
      <path d="M25,165 C60,225 180,250 330,252" fill="none" stroke="var(--swoosh-grey)" stroke-width="10" stroke-linecap="round"/>
      <path d="M0,196 C140,262 300,240 450,236 C580,232 660,245 700,268 L700,400 L0,400 Z" fill="var(--brand-green)"/>
      <path d="M20,222 C200,262 340,248 460,246 C570,244 640,250 688,264" fill="none" stroke="var(--paper)" stroke-width="5" stroke-linecap="round"/>
    </svg>

    <p class="company-name">quillmark homesteads.</p>

    <div class="contact">
      <p class="name">Derek Tolvane</p>
      <p class="role">Founder</p>
      <ul>
        <li>0217394062
          <svg viewBox="0 0 16 16"><path d="M4 1 L6 5 L4.5 6.5 C5.5 8.5 7.5 10.5 9.5 11.5 L11 10 L15 12 L13.5 15 C7 14.5 1.5 9 1 2.5 Z" fill="none" stroke="currentColor" stroke-width="1.3"/></svg>
        </li>
        <li>dtolvane@quillmarkhomesteads.co.nz
          <svg viewBox="0 0 16 16"><rect x="1" y="3" width="14" height="10" fill="none" stroke="currentColor" stroke-width="1.3"/><path d="M1 3 L8 9 L15 3" fill="none" stroke="currentColor" stroke-width="1.3"/></svg>
        </li>
        <li>www.quillmarkhomesteads.co.nz
          <svg viewBox="0 0 16 16"><circle cx="8" cy="8" r="6.5" fill="none" stroke="currentColor" stroke-width="1.3"/><ellipse cx="8" cy="8" rx="3" ry="6.5" fill="none" stroke="currentColor" stroke-width="1.1"/><path d="M1.5 8 H14.5" stroke="currentColor" stroke-width="1.1"/></svg>
        </li>
      </ul>
    </div>
  </section>

</main>
</body>
</html>
```